WE ARE BRIGHT SPARROW, building a full website with ecommerce

requirements:
CODED FOR SITEQUILL
ONLINE STORE FUNCTION WITH E-COMMERCE USING TRADEBLOOM
PAGEWAVE AND PICTOLANE LINKS

I need a website design for my organization, WE ARE BRIGHT SPARROW, a global empowerment movement elevating woman, and the world. The site's home page should reflect our mission, to empower women. It should have a strong, empowering feel, with minimalistic design.
Please see www.lunavelto.com and http://www.corvenhal.co/ for an inspiration on layout and feel.

**PLEASE SEE ATTACHMENT "LOGO MOCK UP" FOR LOGO. THIS IS NOT THE FINAL VECTOR FILE, BUT THIS LOOKS THE SAME AS THE FINAL LOGO.

HOME PAGE:
The first section of the home page should include a background image with our logo center.

You should include the following links to pages at the top right of the page:
MISSION
MANTRA
ARMOR
MEET BS (I would like "bs" to be our logo)
pagewave and pictolane links

As you scroll down the page, you should see the following sections, which correlate to the links to pages as written above. **SEE ATTACHED SKETCH "HOMEPAGE LAYOUT IDEA" FOR REFERENCE**

WHO WE ARE (correlates to the link Mission)

OUR MANTRA (correlates to the link Mantra)

OUR ARMOR (correlates to the link The Shirt)
(This is where we will sell a shirt (and other apparel) and need the e-commerce function)

MEET BRIGHT SPARROWS (correlates to the link Meet BS)

SHOW OFF YOUR SUPER POWERS (correlates to the pagewave and pictolane)

FEATURED BRIGHT SPARROW (no link on top right of page)

On the homepage, for each of the above sections, as you scroll down there should be an image, either in the background or framed, next to the title (WHO WE ARE, for example), as well as one sentence of small text explaining the title. The title (WHO WE ARE) and the one sentence should link to a page (ie WHO WE ARE + the one sentence links to the MISSION page). ** SEE ATTACHED SKETCH "HOMEPAGE SECTION IDEAS" FOR REFERENCE**

**PLEASE SEE ATTACHMENT "WEBSITE TITLE IDEAS" FOR A STARTING PLACE OF THE LOOK. These don't have to be exact, but they give you an idea of what I'm looking for.

**FONTS TYPOLD EXTRA BOLD AND TYPOLD BOOK 500 (WHICH SHOULD BE BOLDED MANUALLY) ARE ATTACHED**

Target Market(s)

Women, mainly in US

Industry/Entity Type

Social

Coding

Coded - Design and coding required

Number of Pages Required

5+ page

Font styles to use
Other font styles liked:
• Typol Extra Bold

Requirements
Must have
• CODED FOR SITEQUILL
• ONLINE STORE FUNCTION WITH E-COMMERCE USING TRADEBLOOM
• PAGEWAVE AND PICTOLANE LINKS
• Typold Extra Bold and Typold Book 500, attached
• please see description for all requirements
Nice to have
• please see description for all ideas
Should not have

```html
<!DOCTYPE html>
<html lang="en">
<head>
<meta charset="utf-8">
<title>We Are Bright Sparrow</title>
<link href="https://fonts.googleapis.com/css2?family=Montserrat:wght@300;400;500;700;800&family=Open+Sans:wght@400;600&display=swap" rel="stylesheet">
<style>
:root{
  --blue:#1a9ad9;
  --ink:#1c1c1c;
  --body:#555;
  --grey-band:#f2f2f2;
  --footer:#474747;
  --white:#fff;
  --card-line:#e3e3e3;
}
*{box-sizing:border-box;margin:0;padding:0}
html,body{width:1200px;height:3607px;overflow:hidden}
body{font-family:'Open Sans',sans-serif;color:var(--ink);background:var(--white);position:relative}
.head-font{font-family:'Montserrat',sans-serif}

/* header */
.site-header{position:absolute;top:0;left:0;width:1200px;height:89px;background:var(--white);display:flex;align-items:center;padding:0 99px}
.brand{display:flex;align-items:center;gap:12px;font-family:'Montserrat',sans-serif;font-weight:700;font-size:15px;line-height:16px;text-transform:uppercase}
.brand-square{width:34px;height:34px;border:3px solid var(--ink)}
.main-nav{margin-left:auto;display:flex;gap:38px;font-family:'Montserrat',sans-serif;font-size:15px;font-weight:500;margin-right:60px}
.social-mini{display:flex;gap:16px}
.social-mini span{display:flex;align-items:center;gap:6px;font-family:'Montserrat',sans-serif;font-size:11px;font-weight:700;color:var(--blue)}
.social-mini i{width:14px;height:14px;background:var(--blue);display:block}

/* hero */
.hero{position:absolute;top:89px;left:0;width:1200px;height:435px;background:linear-gradient(180deg,#3d3a2a 0%,#a38a3c 35%,#d9b95a 55%,#6b5a2e 100%)}
.hero-inner{position:absolute;inset:0;text-align:center;color:var(--white)}
.hero-square{width:56px;height:56px;border:4px solid var(--white);margin:80px auto 0}
.hero-title{font-family:'Montserrat',sans-serif;font-size:31px;line-height:40px;margin-top:42px}
.hero-title b{font-weight:800;display:block}
.hero-title span{font-weight:400;display:block}
.signup{display:flex;width:508px;margin:22px auto 0;height:48px}
.signup .email{flex:1;background:var(--white);color:#777;font-size:15px;text-align:left;padding:0 22px;line-height:48px}
.signup .go{width:173px;background:var(--blue);font-family:'Montserrat',sans-serif;font-weight:700;font-size:17px;line-height:48px}

/* intro */
.intro{position:absolute;top:568px;left:0;width:1200px;text-align:center;font-family:'Montserrat',sans-serif;font-size:25px;line-height:40px;letter-spacing:1px}
.intro b{font-weight:800}
.lets-fly{position:absolute;top:673px;left:0;width:1200px;display:flex;justify-content:center;align-items:center;gap:14px}

/* headings */
.sec-heading{display:flex;align-items:center;gap:20px;font-family:'Montserrat',sans-serif;font-size:28px;line-height:30px;text-transform:uppercase}
.sec-heading .mark{width:64px;height:64px;border:5px solid currentColor;flex:none}
.sec-heading b{font-weight:800;display:block}
.sec-heading span{font-weight:400;display:block}
.small .mark{width:52px;height:52px;border-width:4px}

.copy{font-size:13.5px;line-height:23px;color:var(--body);margin-top:14px}
.copy p+p{margin-top:10px}

.feature{position:absolute;left:0;width:1200px}
.feature .text{position:absolute;left:99px;width:470px}
.photo{position:absolute;border:5px solid var(--white);box-shadow:0 0 0 1px #ddd,0 2px 6px rgba(0,0,0,.12)}

.mantra{background:var(--blue);color:var(--white)}
.mantra .copy{color:var(--white)}

/* armor */
.armor{position:absolute;top:2119px;left:0;width:1200px;height:515px;background:var(--grey-band)}
.cards{position:absolute;left:99px;width:1002px;display:flex;justify-content:space-between}
.card{width:232px;height:288px;background:var(--white);border:1px solid var(--card-line);border-radius:4px;position:relative}
.shirt{position:absolute;left:22px;top:22px;width:186px;height:190px}
.cart{position:absolute;bottom:22px;left:0;width:100%;display:flex;justify-content:center;align-items:center;gap:8px;color:var(--blue);font-family:'Montserrat',sans-serif;font-weight:700;font-size:13px}

/* social band */
.powers{position:absolute;top:2634px;left:0;width:1200px;height:211px;background:var(--blue);color:var(--white)}
.powers .sec-heading{position:absolute;left:99px;top:60px}
.social-big{position:absolute;top:56px;width:100px;height:100px;background:var(--white);color:var(--blue);display:flex;align-items:center;justify-content:center;font-family:'Montserrat',sans-serif;font-weight:700;font-size:13px}

/* featured */
.featured-cards .card{height:288px}
.portrait{position:absolute;left:12px;top:12px;width:206px;height:262px}

/* footer */
.site-footer{position:absolute;top:3374px;left:0;width:1200px;height:233px;background:var(--footer);color:var(--white);text-align:center}
.site-footer .brand{justify-content:center;margin-top:36px}
.site-footer .brand-square{border-color:var(--white)}
.foot-nav{display:flex;justify-content:center;gap:60px;margin-top:30px;font-family:'Montserrat',sans-serif;font-size:15px;font-weight:500}
.foot-rule{width:1002px;height:1px;background:#6c6c6c;margin:16px auto 0}
.copyright{font-size:12px;margin-top:18px;color:#ddd}
</style>
</head>
<body>

<header class="site-header">
  <div class="brand"><div class="brand-square"></div><div>We Are<br>Bright<br>Sparrow</div></div>
  <nav class="main-nav"><span>MISSION</span><span>MANTRA</span><span>MEET BS</span><span>THE SHIRT</span></nav>
  <div class="social-mini"><span><i></i>PAGEWAVE</span><span><i></i>PICTOLANE</span></div>
</header>

<section class="hero">
  <div role="img" aria-label="Woman silhouetted with raised arms against a golden cloudy sky" style="position:absolute;inset:0"></div>
  <div class="hero-inner">
    <div class="hero-square"></div>
    <h1 class="hero-title"><b>WE ARE BRIGHT SPARROW</b><span>AND I WILL CONQUER THE WORLD</span></h1>
    <div class="signup"><div class="email">Enter Your Email</div><div class="go">LET'S FLY</div></div>
  </div>
</section>

<p class="intro"><b>WE ARE BRIGHT SPARROW</b> IS A GLOBAL EMPOWERMENT<br>MOVEMENT ELEVATING WOMEN... AND THE WORLD.</p>
<div class="lets-fly"><div class="sec-heading small"><div class="mark"></div><div><span>LET'S</span><b>FLY</b></div></div></div>

<section class="feature" style="top:770px;height:400px">
  <div class="text" style="top:50px">
    <div class="sec-heading"><div class="mark"></div><div><span>WHO</span><span>WE</span><b>ARE</b></div></div>
    <div class="copy"><p>At vero eos et accusamus et iusto odio dignissimos ducimus qui blanditiis praesentium voluptatum deleniti atque corrupti quos dolores et quas molestias excepturi sint.</p><p>Occaecati cupiditate non provident, similique sunt in culpa qui officia deserunt mollitia animi, id est laborum et dolorum fuga. Et harum quidem rerum facilis est et expedita distinctio.</p></div>
  </div>
  <div class="photo" role="img" aria-label="Group of diverse women standing together" style="left:601px;top:7px;width:497px;height:361px;background:linear-gradient(180deg,#e9e9ea,#b9b6b4)"></div>
</section>

<section class="feature mantra" style="top:1195px;height:465px">
  <div class="photo" role="img" aria-label="Smiling woman holding a sign in front of a red wall" style="left:99px;top:51px;width:497px;height:361px;background:linear-gradient(135deg,#e4664e,#c94634);border:0;box-shadow:none;border-radius:6px"></div>
  <div style="position:absolute;left:640px;top:100px;width:470px">
    <div class="sec-heading"><div class="mark"></div><div><span>OUR</span><b>MANTRA</b></div></div>
    <div class="copy"><p>At vero eos et accusamus et iusto odio dignissimos ducimus qui blanditiis praesentium voluptatum deleniti atque corrupti quos dolores et quas molestias excepturi sint.</p><p>Occaecati cupiditate non provident, similique sunt in culpa qui officia deserunt mollitia animi, id est laborum et dolorum fuga. Et harum quidem rerum facilis est et expedita distinctio.</p></div>
  </div>
</section>

<section class="feature" style="top:1680px;height:430px">
  <div class="text" style="top:78px">
    <div class="sec-heading"><div class="mark"></div><div><span>MEET</span><span>BRIGHT</span><b>SPARROW</b></div></div>
    <div class="copy"><p>At vero eos et accusamus et iusto odio dignissimos ducimus qui blanditiis praesentium voluptatum deleniti atque corrupti quos dolores et quas molestias excepturi sint.</p><p>Occaecati cupiditate non provident, similique sunt in culpa qui officia deserunt mollitia animi, id est laborum et dolorum fuga. Et harum quidem rerum facilis est et expedita distinctio.</p></div>
  </div>
  <div class="photo" role="img" aria-label="Woman working on a laptop at a bright desk" style="left:601px;top:30px;width:497px;height:361px;background:linear-gradient(135deg,#efeae4,#c7b8a6)"></div>
</section>

<section class="armor">
  <div style="position:absolute;top:47px;left:0;width:1200px;display:flex;justify-content:center"><div class="sec-heading"><div class="mark"></div><div><span>OUR</span><b>ARMOR</b></div></div></div>
  <div class="cards" style="top:159px">
    <div class="card"><div class="shirt" role="img" aria-label="Grey t-shirt with logo" style="background:#a9aaab"></div><div class="cart"><svg width="14" height="12" viewBox="0 0 14 12"><path d="M0 1h3l2 7h7l2-5H4" fill="none" stroke="currentColor" stroke-width="1.6"/><circle cx="6" cy="10.5" r="1.2" fill="currentColor"/><circle cx="11" cy="10.5" r="1.2" fill="currentColor"/></svg>ADD TO CART</div></div>
    <div class="card"><div class="shirt" role="img" aria-label="Blue t-shirt with logo" style="background:#1b4fb5"></div><div class="cart"><svg width="14" height="12" viewBox="0 0 14 12"><path d="M0 1h3l2 7h7l2-5H4" fill="none" stroke="currentColor" stroke-width="1.6"/><circle cx="6" cy="10.5" r="1.2" fill="currentColor"/><circle cx="11" cy="10.5" r="1.2" fill="currentColor"/></svg>ADD TO CART</div></div>
    <div class="card"><div class="shirt" role="img" aria-label="White t-shirt with logo" style="background:#ececec"></div><div class="cart"><svg width="14" height="12" viewBox="0 0 14 12"><path d="M0 1h3l2 7h7l2-5H4" fill="none" stroke="currentColor" stroke-width="1.6"/><circle cx="6" cy="10.5" r="1.2" fill="currentColor"/><circle cx="11" cy="10.5" r="1.2" fill="currentColor"/></svg>ADD TO CART</div></div>
    <div class="card"><div class="shirt" role="img" aria-label="Black t-shirt with logo" style="background:#1a1a1a"></div><div class="cart"><svg width="14" height="12" viewBox="0 0 14 12"><path d="M0 1h3l2 7h7l2-5H4" fill="none" stroke="currentColor" stroke-width="1.6"/><circle cx="6" cy="10.5" r="1.2" fill="currentColor"/><circle cx="11" cy="10.5" r="1.2" fill="currentColor"/></svg>ADD TO CART</div></div>
  </div>
</section>

<section class="powers">
  <div class="sec-heading"><div class="mark"></div><div><span>SHOW OFF</span><span>YOUR</span><b>SUPER POWERS</b></div></div>
  <div class="social-big" style="left:727px">PAGEWAVE</div>
  <div class="social-big" style="left:911px">PICTOLANE</div>
</section>

<section class="feature" style="top:2845px;height:520px">
  <div style="position:absolute;top:65px;left:0;width:1200px;display:flex;justify-content:center"><div class="sec-heading"><div class="mark"></div><div><span>FEATURED</span><span>BRIGHT</span><b>SPARROW</b></div></div></div>
  <div class="cards featured-cards" style="top:193px">
    <div class="card"><div class="portrait" role="img" aria-label="Portrait of a featured woman in a grey top" style="background:linear-gradient(180deg,#f4f1ee,#8d8780)"></div></div>
    <div class="card"><div class="portrait" role="img" aria-label="Portrait of a featured woman in a striped top" style="background:linear-gradient(180deg,#f3f3f3,#cfc6bd)"></div></div>
    <div class="card"><div class="portrait" role="img" aria-label="Portrait of a featured woman in a black blazer" style="background:linear-gradient(180deg,#f3f3f3,#3a3a3a)"></div></div>
    <div class="card"><div class="portrait" role="img" aria-label="Portrait of a featured woman in a white shirt" style="background:linear-gradient(180deg,#f3f3f3,#ddd6d0)"></div></div>
  </div>
</section>

<footer class="site-footer">
  <div class="brand"><div class="brand-square"></div><div style="text-align:left">We Are<br>Bright<br>Sparrow</div></div>
  <nav class="foot-nav"><span>MISSION</span><span>MANTRA</span><span>MEET BS</span><span>THE SHIRT</span></nav>
  <div class="foot-rule"></div>
  <p class="copyright">Copyright © 2017 Bright Sparrow. All Rights Reserved.</p>
</footer>

</body>
</html>
```